High Tech Real Estate Startup needs a business card

We are developing an innovative real estate marketing product based around advanced search and virtual reality.

We talk to people, we need business cards.

Target Market(s)

The target market is technology professionals and realtors.

Contact Information for Business Card

The information to be included will include

Name
Title
Phone Number
E-mail Address
www.zelquin.com

It should use simple iconography for each one of those fields.

Font styles to use
Other font styles liked:
• Co, Jubilat, Avenir

Colors

Designer to choose colors to be used in the design.

Requirements
Must have
• Clean aesthetic,
• Good use of negative space.
• It should use our company logo, shown in the attached file. It is able to use the negative of that logo (coloured font and white background) and I have attached other acceptable accent colours in a swatch file.
Should not have
• Should not be too busy
• No extraneous text (slogans, tag lines etc)

```html
<!DOCTYPE html>
<html lang="en">
<head>
<meta charset="utf-8">
<title>Zelquin Business Card</title>
<link href="https://fonts.googleapis.com/css2?family=Montserrat:wght@500&family=Roboto:wght@400;500&display=swap" rel="stylesheet">
<style>
  :root {
    --teal: #14b9be;
    --charcoal: #2a2a2c;
    --paper: #ffffff;
    --ink: #1f1f1f;
    --backdrop: #3a3530;
  }
  * { box-sizing: border-box; margin: 0; padding: 0; }
  html, body { width: 1200px; height: 930px; overflow: hidden; }
  body {
    background: var(--backdrop);
    position: relative;
    font-family: "Roboto", Arial, sans-serif;
  }
  .card {
    position: absolute;
    width: 540px;
    height: 309px;
    border-radius: 16px;
    overflow: hidden;
  }
  .card-front {
    left: 80px; top: 130px;
    background: var(--teal);
    display: flex; align-items: center; justify-content: center;
  }
  .wordmark {
    font-family: "Montserrat", Arial, sans-serif;
    font-weight: 500;
    letter-spacing: 6px;
  }
  .card-front .wordmark { color: var(--paper); font-size: 72px; }
  .card-back { left: 580px; top: 490px; background: var(--paper); }
  .swoosh { position: absolute; inset: 0; }
  .card-back .wordmark {
    position: absolute; right: 70px; top: 36px;
    color: var(--teal); font-size: 52px;
  }
  .person { position: absolute; left: 34px; top: 124px; }
  .name-row {
    display: flex; align-items: flex-end; gap: 10px;
    width: 446px;
  }
  .person-name {
    color: var(--teal); font-weight: 500; font-size: 22px; letter-spacing: 0.5px;
    line-height: 26px; white-space: nowrap; flex: none;
  }
  .divider { flex: 1; height: 2px; background: var(--teal); margin-bottom: 6px; }
  .person-title { color: var(--ink); font-size: 14px; margin-top: 2px; }
  .address { color: var(--ink); font-size: 14px; line-height: 18px; margin-top: 12px; }
  .contact { list-style: none; margin-top: 12px; color: var(--ink); font-size: 14px; line-height: 19px; }
  .contact li { display: flex; align-items: center; gap: 8px; }
  .contact svg { width: 11px; height: 11px; flex: none; }
</style>
</head>
<body>
  <section class="card card-front">
    <span class="wordmark">ZELQUIN</span>
  </section>

  <section class="card card-back">
    <svg class="swoosh" viewBox="0 0 540 309" aria-hidden="true">
      <path d="M476 0 C525 80 512 210 420 309 L540 309 L540 0 Z" fill="var(--charcoal)"/>
      <path d="M494 0 C538 90 524 215 438 309 L540 309 L540 0 Z" fill="var(--teal)"/>
    </svg>
    <span class="wordmark">ZELQUIN</span>
    <div class="person">
      <div class="name-row">
        <p class="person-name">DANA WHITLOCK</p>
        <span class="divider"></span>
      </div>
      <p class="person-title">Director</p>
      <p class="address">482 Alder Creek Rd.<br>Franklin, TN 37064</p>
      <ul class="contact">
        <li><svg viewBox="0 0 12 12"><path d="M2 1 L4.5 1 L5.5 3.5 L4 4.5 C4.7 6 6 7.3 7.5 8 L8.5 6.5 L11 7.5 L11 10 C6 10.5 1.5 6 2 1 Z" fill="var(--teal)"/></svg>+1-555-014-2290</li>
        <li><svg viewBox="0 0 12 12"><rect x="1" y="2.5" width="10" height="7" fill="none" stroke="var(--teal)" stroke-width="1.2"/><path d="M1 2.5 L6 6.5 L11 2.5" fill="none" stroke="var(--teal)" stroke-width="1.2"/></svg>info@zelquin.com</li>
        <li><svg viewBox="0 0 12 12"><circle cx="6" cy="6" r="5" fill="none" stroke="var(--teal)" stroke-width="1.2"/><ellipse cx="6" cy="6" rx="2.2" ry="5" fill="none" stroke="var(--teal)" stroke-width="1"/><path d="M1 6 H11" stroke="var(--teal)" stroke-width="1"/></svg>www.zelquin.com</li>
      </ul>
    </div>
  </section>
</body>
</html>
```